Satchel & Sundial needs new business card design

I need a new business card design. I'm looking for out-of-the-box design which represents the freedom of being a location independent entrepreneur.
I offer coaching, retreats and trips.
I would like to see designs with and without the photo.
Colors I use are black (#000000), green (#25A796) and brown (#D7C38C)
Website satchelandsundial.example

Target Market(s)

location independent entrepreneurs, digital nomads, people looking to swap the 9 to 5 for a lifestyle business

Industry/Entity Type

Business

Contact Information for Business Card

Dorota Falkner
Your Lifestyle Business Coach, Retreat & Trip Leader
http://satchelandsundial.example
hello@satchelandsundial.example
Live a life you don't need a holiday from

Font styles to use
Serif
Sans Serif

Requirements
Must have
• One side should contain only the logo. I would also consider having the "Live a life you don't need a holiday from" on that side too (depending on how it looks)
• Please show both sides on the designs.

```html
<!DOCTYPE html>
<html lang="en">
<head>
<meta charset="utf-8">
<title>Satchel &amp; Sundial — Business Card</title>
<link rel="stylesheet" href="https://fonts.googleapis.com/css2?family=Open+Sans:ital,wght@0,400;0,600;0,700;1,400&display=swap">
<style>
  :root {
    --ink: #1a1a1a;
    --text: #2b2b2b;
    --muted: #444444;
    --teal: #25a796;
    --card: #ffffff;
    --backdrop: #e9e9e9;
    --pattern-light: #f7f7f7;
    --pattern-mid: #efefef;
  }
  * { box-sizing: border-box; margin: 0; padding: 0; }
  html, body {
    width: 1105px;
    height: 1200px;
    overflow: hidden;
  }
  body {
    background: var(--backdrop);
    font-family: "Open Sans", Arial, sans-serif;
    color: var(--text);
    position: relative;
  }
  .card {
    position: absolute;
    left: 196px;
    width: 720px;
    height: 410px;
    background: var(--card);
  }
  .card--front { top: 146px; }
  .card--back  { top: 602px; }

  /* Front */
  .wordmark {
    font-family: "Open Sans", Arial, sans-serif;
    font-weight: 700;
    color: var(--ink);
    white-space: nowrap;
  }
  .card--front .wordmark {
    position: absolute;
    top: 62px;
    right: 46px;
    font-size: 32px;
  }
  .holder {
    position: absolute;
    left: 47px;
    top: 214px;
  }
  .holder__name {
    font-size: 23px;
    font-weight: 700;
    color: var(--teal);
    letter-spacing: 0.5px;
    text-transform: uppercase;
    line-height: 1.2;
  }
  .holder__role {
    font-size: 19px;
    color: var(--ink);
    line-height: 1.35;
  }
  .contact {
    position: absolute;
    left: 47px;
    top: 315px;
    list-style: none;
  }
  .contact__item {
    display: flex;
    align-items: center;
    gap: 10px;
    font-size: 18px;
    color: var(--muted);
    height: 28px;
  }
  .contact__icon { width: 17px; height: 17px; flex: none; }

  /* Back */
  .pattern {
    position: absolute;
    inset: 0;
    background: linear-gradient(160deg, var(--pattern-light), var(--pattern-mid) 50%, var(--pattern-light));
  }
  .social {
    position: absolute;
    top: 26px;
    right: 24px;
    display: flex;
    gap: 4px;
  }
  .social__tile {
    width: 25px;
    height: 25px;
    background: var(--teal);
  }
  .card--back .wordmark {
    position: absolute;
    top: 180px;
    left: 0;
    right: 0;
    text-align: center;
    font-size: 52px;
  }
  .motto {
    position: absolute;
    top: 352px;
    left: 0;
    right: 0;
    text-align: center;
    font-size: 19px;
    font-style: italic;
    color: var(--ink);
  }
</style>
</head>
<body>

  <section class="card card--front" aria-label="Card front">
    <div class="wordmark">Satchel &amp; Sundial</div>

    <div class="holder">
      <p class="holder__name">Dorota Falkner</p>
      <p class="holder__role">Your Lifestyle Business Coach</p>
      <p class="holder__role">Retreat &amp; Trip Leader</p>
    </div>

    <ul class="contact">
      <li class="contact__item">
        <svg class="contact__icon" viewBox="0 0 17 17" aria-hidden="true">
          <rect x="1" y="3.5" width="15" height="10" fill="var(--teal)"/>
          <path d="M1.5 4 L8.5 9.5 L15.5 4" fill="none" stroke="#fff" stroke-width="1.3"/>
        </svg>
        <span>hello@satchelandsundial.example</span>
      </li>
      <li class="contact__item">
        <svg class="contact__icon" viewBox="0 0 17 17" aria-hidden="true">
          <circle cx="8.5" cy="8.5" r="7.5" fill="var(--teal)"/>
          <path d="M1.5 8.5 H15.5 M8.5 1 C5 5 5 12 8.5 16 M8.5 1 C12 5 12 12 8.5 16" fill="none" stroke="#fff" stroke-width="1.1"/>
        </svg>
        <span>www.satchelandsundial.example</span>
      </li>
    </ul>
  </section>

  <section class="card card--back" aria-label="Card back">
    <div class="pattern" role="img" aria-label="Faint repeating brand lettering pattern across the card"></div>

    <div class="social" aria-label="Social profiles">
      <span class="social__tile"></span>
      <span class="social__tile"></span>
      <span class="social__tile"></span>
    </div>

    <div class="wordmark">Satchel &amp; Sundial</div>
    <p class="motto">Live a life you don't need a holiday from</p>
  </section>

</body>
</html>
```